$5 Quest Website Required

I am looking for someone to develop a website akin to the simplicity of www.boxlantern.example with a video in the center or a tab that permits one to "Accept the Challenge."

Incorporates our logo and is used to promote our "$5 Quest Program."

Please see attachments, but we are igniting entrepreneurial spirit among our nation's youth through this interactive and intensive program!

There should be a way to navigate to other sections of the site including:

About
Why
Request $5 Quest Packet
Success Stories
Partners
Link to Norvik Holdings
Updates

Thanks to all in advance!

Looking forward to working with you!

Good feel of what we are looking for in terms of "feel"

http://www.thebrightripple.example/

Thank you,

RB

Please make note of this website, we are going for a feel that is akin to this and less modern and professional...more abstract and interactive...but of course include space for our video:

Colors, feel, imagery, is great. Keep your formats, but bring on the feel!

Thank you all for your hard work and patience.

Thank you all for your hard work thus far.

Meanwhile, please understand that the $5 Quest is young, youthful, full of challenge and vitality, it is a competition among students from high school and universities.  The websites you have delivered are too corporate, stale, and standard.  I'm looking for something that is fresh, different, like www.thebrightripple.example.

Symbols, cartoonish, but serious, down to business and save the world one $5 bill at a time.  The logo can be used as a theme...the colors, the feel.

Video space for explanation on the $5 Quest front and center.  With leaves, $ signs, colorful colors, etc.

Visual needs to be compelling to Join the Challenge! Although Norvik Holdings and the tree is a parent company; $5 Quest is separate and Norvik Holdings should only be mentioned as a link.

PixelHarbor.example in regard to simplicity; and www.thebrightripple.example in terms of style.

Thank you,

Raphael

Like the designs that have been submitted; we are almost there.

Target Market(s)

Professors, students, teachers, parents and NGO leaders who wish to use our program as a way to inspire leadership/entrepreneurship/fundraise for their causes.

Requirements
Must have
• Place for the video, front and center
Include logo
Forsight for blogging, message, etc.
Nice to have
• Plan "buckets" to include"
Explanation Video
Two pamphlets
Contract
FAQs
Website with Blog, voting, registration, video upload, etc.
Flyer perfected
Parable...symbol of our life
Photos
Stats included
Testimonials
Organizations that have used (TKWLM, North Brook Lodge, Marlowton High)
Sponsors (Open Lantern, Copperleaf Learningfield)
Photos from events

I understand this takes coding and such, but want you to be aware of the long term vision for it!

```html
<!DOCTYPE html>
<html lang="en">
<head>
<meta charset="utf-8">
<title>$5 Quest</title>
<link rel="stylesheet" href="https://fonts.googleapis.com/css2?family=Oswald:wght@400;500&family=Open+Sans:wght@400;600&family=Arimo:wght@400;700&display=swap">
<style>
  :root {
    --green: #3cb94a;
    --green-dark: #1f7d2a;
    --yellow: #dce233;
    --yellow-light: #eef27a;
    --yellow-text: #f0ee3c;
    --olive: #8a8a1a;
    --orange: #ffa200;
    --ink: #111111;
    --grey-logo: #555555;
    --grey-footer: #333333;
    --white: #ffffff;
    --frame-grey: #dedede;
    --ribbon: #3b3b3b;
    --ribbon-edge: #2a2a2a;
  }
  * { margin: 0; padding: 0; box-sizing: border-box; }
  html, body { width: 1200px; height: 982px; overflow: hidden; background: var(--white); }
  body { position: relative; font-family: "Arimo", Arial, sans-serif; color: var(--ink); }

  .site-header { position: absolute; left: 0; top: 0; width: 1200px; height: 216px; background: var(--white); }
  .utility-nav { position: absolute; right: 34px; top: 0; display: flex; align-items: center; height: 29px; font-family: "Oswald", sans-serif; font-size: 16px; letter-spacing: .5px; }
  .utility-nav a { color: var(--ink); text-decoration: none; margin-right: 22px; padding-top: 2px; }
  .language-button { background: var(--orange); color: var(--ink); height: 29px; width: 105px; border-radius: 0 0 3px 3px; display: flex; align-items: center; justify-content: space-between; padding: 0 10px 0 8px; font-size: 14px; font-weight: 500; }
  .language-button svg { width: 12px; height: 10px; }

  .brand { position: absolute; left: 300px; top: 26px; display: flex; align-items: center; }
  .brand-mark { width: 150px; height: 150px; border-radius: 50%; background: var(--green); margin-right: 26px; }
  .brand-name { font-family: "Open Sans", sans-serif; font-weight: 600; font-size: 92px; color: var(--grey-logo); letter-spacing: 1px; }

  .main-nav { position: absolute; left: 0; top: 216px; width: 1200px; height: 60px; background: var(--yellow); border-top: 4px solid var(--yellow-light); border-bottom: 3px solid var(--yellow-light); display: flex; justify-content: center; align-items: center; font-family: "Oswald", sans-serif; font-size: 21px; letter-spacing: .6px; }
  .main-nav a { color: var(--ink); text-decoration: none; }
  .main-nav a.is-current { color: var(--olive); }
  .main-nav .nav-dot { width: 6px; height: 6px; border-radius: 50%; background: var(--green-dark); margin: 0 20px; }

  .hero { position: absolute; left: 0; top: 276px; width: 1200px; height: 626px; background: var(--green); }
  .section-title { font-family: "Open Sans", sans-serif; font-size: 21px; color: var(--white); padding-bottom: 10px; border-bottom: 2px dotted rgba(255,255,255,.75); text-shadow: 0 1px 1px rgba(0,0,0,.25); }
  .section-title em { font-style: normal; color: var(--yellow-text); }

  .welcome { position: absolute; left: 24px; top: 54px; width: 314px; }
  .welcome p { font-size: 14.6px; line-height: 21px; color: var(--white); text-align: justify; margin-top: 9px; }
  .welcome .section-title { margin-bottom: 16px; }

  .video-panel { position: absolute; left: 394px; top: 22px; width: 534px; height: 445px; background: var(--white); border: 3px solid #f4f7c8; border-radius: 6px; box-shadow: 0 40px 30px -32px rgba(0,0,0,.45); padding: 7px; }
  .video-screen { width: 100%; height: 100%; border: 6px solid var(--frame-grey); background: var(--white); position: relative; }
  .play-button { position: absolute; left: 165px; top: 87px; width: 176px; height: 176px; }
  .watch-label { position: absolute; left: 0; right: 0; top: 298px; text-align: center; font-family: "Oswald", sans-serif; font-size: 29px; color: #222; letter-spacing: .5px; }
  .watch-label-reflection { top: 332px; transform: scaleY(-1); opacity: .18; }

  .accept-challenge { position: absolute; left: 294px; top: 508px; width: 702px; height: 80px; }
  .accept-challenge .dash-line { position: absolute; left: 0; right: 0; top: 36px; border-top: 2px dashed rgba(20,60,20,.75); }
  .accept-challenge svg { position: absolute; left: 150px; top: 4px; width: 398px; height: 66px; }
  .accept-label { position: absolute; left: 150px; top: 4px; width: 398px; height: 66px; display: flex; align-items: center; justify-content: center; font-family: "Open Sans", sans-serif; font-size: 23px; color: #a9a9a9; letter-spacing: .5px; }

  .testimonials { position: absolute; left: 972px; top: 54px; width: 204px; }
  .testimonials .section-title { text-align: right; margin-bottom: 16px; }
  .testimonial { position: relative; margin-bottom: 26px; }
  .testimonial .quote-mark { position: absolute; left: -30px; top: -20px; font-family: Georgia, serif; font-size: 110px; line-height: 1; color: rgba(0,0,0,.1); }
  .testimonial blockquote { position: relative; width: 170px; font-size: 14.6px; line-height: 19px; color: var(--white); text-align: justify; margin-left: 12px; }
  .testimonial cite { display: block; text-align: right; font-style: normal; font-size: 14.6px; margin-top: 10px; color: var(--ink); }

  .site-footer { position: absolute; left: 0; top: 902px; width: 1200px; height: 80px; background: var(--white); border-top: 1px solid #e4e4e4; }
  .footer-brand { position: absolute; left: 40px; top: 20px; display: flex; align-items: center; }
  .footer-brand .brand-mark { width: 30px; height: 30px; margin-right: 8px; }
  .footer-brand .brand-name { font-size: 22px; letter-spacing: 0; }
  .footer-nav { position: absolute; right: 40px; top: 24px; display: flex; font-size: 13.5px; }
  .footer-nav a { color: var(--grey-footer); text-decoration: none; margin-left: 20px; }
  .copyright { position: absolute; right: 40px; top: 51px; font-size: 13px; color: var(--grey-footer); }
</style>
</head>
<body>
  <header class="site-header">
    <nav class="utility-nav">
      <a href="#">FAQ</a>
      <a href="#">SIGNIN</a>
      <span class="language-button">LANGUAGE
        <svg viewBox="0 0 12 10"><path d="M0 0h12L6 10z" fill="#111"/></svg>
      </span>
    </nav>
    <div class="brand">
      <span class="brand-mark"></span>
      <span class="brand-name">$5 Quest</span>
    </div>
  </header>

  <nav class="main-nav">
    <a href="#" class="is-current">HOME</a><span class="nav-dot"></span>
    <a href="#">ABOUT US</a><span class="nav-dot"></span>
    <a href="#">WHY WE ARE?</a><span class="nav-dot"></span>
    <a href="#">SUCCESS STORIES</a><span class="nav-dot"></span>
    <a href="#">PARTNERS</a><span class="nav-dot"></span>
    <a href="#">NORVIK HOLDINGS</a>
  </nav>

  <main class="hero">
    <section class="welcome">
      <h2 class="section-title">WELCOME TO <em>$5 QUEST</em></h2>
      <p>Lorem ipsum dolor sit amet, consectetur adipiscing elit. Curabitur eu nisl odio. Cras egestas turpis in mi feugiat vel tincidunt arcu accumsan. Phasellus non posuere eros. Aenean consectetur.</p>
      <p>sapien in elit luctus ac posuere purus placerat. Aliquam turpis lorem,.</p>
      <p>Donec fermentum sodales erat, quis consequat nisi ornare eget. Duis volutpat justo ut ante imperdiet feugiat. &nbsp;fermentum sodales erat, quis consequat nisi ornare eget. Duis volutpat justo ut ante imperdiet feugiat.</p>
      <p>sapien in elit luctus ac posuere purus placerat. Aliquam turpis lorem,.</p>
    </section>

    <section class="video-panel">
      <div class="video-screen">
        <svg class="play-button" viewBox="0 0 176 176" aria-label="Play video">
          <defs>
            <linearGradient id="playFace" x1="0" y1="0" x2="0" y2="1">
              <stop offset="0" stop-color="#0d0d0d"/>
              <stop offset="1" stop-color="#3a3a3a"/>
            </linearGradient>
            <linearGradient id="playArrow" x1="0" y1="0" x2="0" y2="1">
              <stop offset="0" stop-color="#f2f2f2"/>
              <stop offset="1" stop-color="#9a9a9a"/>
            </linearGradient>
          </defs>
          <circle cx="88" cy="88" r="87" fill="url(#playFace)"/>
          <path d="M72 54 L116 88 L72 122 Z" fill="url(#playArrow)"/>
        </svg>
        <div class="watch-label">WATCH VIDEO</div>
        <div class="watch-label watch-label-reflection" aria-hidden="true">WATCH VIDEO</div>
      </div>
    </section>

    <div class="accept-challenge">
      <span class="dash-line"></span>
      <svg viewBox="0 0 398 66" aria-hidden="true">
        <path d="M0 0 H398 L384 33 L398 66 H0 L14 33 Z" fill="var(--ribbon-edge)"/>
        <path d="M22 7 H376 L366 33 L376 59 H22 L32 33 Z" fill="var(--ribbon)"/>
      </svg>
      <a class="accept-label" href="#">ACCEPT THE CHALLENGE</a>
    </div>

    <aside class="testimonials">
      <h2 class="section-title">Client <em>Testimonials</em></h2>
      <figure class="testimonial">
        <span class="quote-mark" aria-hidden="true">&ldquo;</span>
        <blockquote>Lorem ipsum dolor sit amsectetur adipiscing elit. Curabitur eu nisl odio. dolor sit amsectetur u nisl odio.</blockquote>
        <cite>- LOREM IPSUM</cite>
      </figure>
      <figure class="testimonial">
        <span class="quote-mark" aria-hidden="true">&ldquo;</span>
        <blockquote>Lorem ipsum dolor sit amsectetur adipiscing elit. Curabitur eu nisl odio. dolor sit amsectetur u nisl odio.</blockquote>
        <cite>- LOREM IPSUM</cite>
      </figure>
    </aside>
  </main>

  <footer class="site-footer">
    <div class="footer-brand">
      <span class="brand-mark"></span>
      <span class="brand-name">$5 Quest</span>
    </div>
    <nav class="footer-nav">
      <a href="#">Home</a>
      <a href="#">About Us</a>
      <a href="#">Success Stories</a>
      <a href="#">Partners</a>
      <a href="#">Norvik Holdings</a>
      <a href="#">Terms</a>
      <a href="#">Privacy Policy</a>
    </nav>
    <p class="copyright">All Rights reserved @ $5quest</p>
  </footer>
</body>
</html>
```